K&R Trailer Rental promo Flyer 5.5x8.5" Flyer

All assets and several pictures of my trailers, that we rent out, are attached.

Flyer dimensions are 5.5"x8.5" - I'll be having it printed on glossy stock.
The dimensions and capacity of the trailers is key.
Include phone number: 555-613-2890 and our website kandrtrailer-example.com

I want something that will really "POP".

Target Market(s)

Blue collar business owners. Recreational offer roads/4x4 folks, used car dealers, contractors/small business owners. Folks with only occasional need for a trailer

Industry/Entity Type

Trailer Rental

Font styles to use
Other font styles liked:
• Designer's choice/no preference

Colors
EE7325
F08F49
F5BC92
FAE3D3
FDF4ED

Requirements
Must have
• Phone number, website, and details about our trailer offerings

```html
<!DOCTYPE html>
<html lang="en">
<head>
<meta charset="utf-8">
<title>K&amp;R Trailer Rental – Car or Equipment Trailers</title>
<link rel="stylesheet" href="https://fonts.googleapis.com/css2?family=Montserrat:wght@800;900&family=Oswald:wght@300;500;600&family=Poppins:wght@400;500;600;700&display=swap">
<style>
  :root{
    --sky-top:#3fb6ea;
    --sky-bright:#e9f8ff;
    --asphalt:#2a2a2c;
    --ink:#232323;
    --teal:#4aa4aa;
    --teal-light:#dcf6fb;
    --coral:#d9675d;
    --coral-light:#fde7e4;
    --white:#ffffff;
  }
  *{box-sizing:border-box;margin:0;padding:0}
  html,body{width:806px;height:1200px;overflow:hidden;background:#e9e9e9}
  .flyer{
    position:relative;width:806px;height:1200px;overflow:hidden;
    background:linear-gradient(180deg,var(--sky-top) 0%,#49c3ee 25%,var(--asphalt) 62%,#1d1d1f 100%);
    font-family:"Poppins",sans-serif;color:var(--white);
  }
  .sun-glow{position:absolute;left:-120px;top:-40px;width:520px;height:520px;border-radius:50%;
    background:radial-gradient(circle,var(--sky-bright) 0%,rgba(233,248,255,.6) 35%,rgba(233,248,255,0) 70%)}
  .hero-photo{position:absolute;left:0;top:300px;width:806px;height:470px;
    background:linear-gradient(180deg,rgba(75,170,220,0) 0%,#7d9fb8 12%,#d9b64a 26%,#c9a23c 34%,#4a4a4c 46%,#333335 75%,rgba(42,42,44,0) 100%)}
  .brand{position:absolute;left:60px;top:150px;display:flex;align-items:center;gap:10px}
  .brand-dot{width:14px;height:14px;background:var(--ink)}
  .brand-name{font-family:"Poppins",sans-serif;font-weight:600;font-size:20px;color:var(--ink);letter-spacing:.5px}
  .headline{position:absolute;left:366px;top:40px;color:var(--ink);font-family:"Montserrat",sans-serif;font-weight:900;line-height:1}
  .headline-car{font-size:118px;letter-spacing:-4px;display:block}
  .headline-or{position:absolute;left:292px;top:18px;width:88px;height:88px;border-radius:50%;background:var(--coral);
    color:var(--white);font-size:30px;display:flex;align-items:center;justify-content:center}
  .headline-equipment{display:block;font-size:60px;letter-spacing:-2.5px;margin-top:4px}
  .headline-trailers{display:inline-block;margin-top:10px;background:var(--coral);color:var(--white);
    font-size:42px;letter-spacing:1px;padding:6px 12px}
  .offer-intro{position:absolute;left:60px;top:722px;font-family:"Oswald",sans-serif;font-size:30px;line-height:34px;text-transform:uppercase}
  .offer-intro .thin{font-weight:300;color:var(--white);display:block}
  .offer-intro .bold{font-weight:600;color:var(--teal);display:block}
  .features{position:absolute;left:60px;top:912px;width:262px;list-style:none}
  .feature{display:flex;align-items:center;gap:14px;padding:8px 0;border-bottom:1px dashed #777;font-weight:600;font-size:16px;line-height:19px}
  .feature:last-child{border-bottom:none}
  .feature svg{width:34px;height:34px;flex:none}
  .trailer{position:absolute;top:565px;width:232px}
  .trailer-car{left:267px}
  .trailer-equip{left:515px}
  .trailer-photo{position:absolute;left:55px;width:152px;height:152px;border-radius:50%;border:4px solid var(--teal)}
  .trailer-car .trailer-photo{background:linear-gradient(180deg,#a9d4f0 0%,#d9dcdf 45%,#8f8f93 70%,#3a3a3c 100%)}
  .trailer-equip .trailer-photo{background:linear-gradient(180deg,#9fd0f2 0%,#7fa56a 30%,#d6d6d6 50%,#5d5d60 80%,#3b3b3d 100%)}
  .trailer-head{position:absolute;left:40px;top:122px;width:180px;height:80px;background:var(--teal);border-radius:90px 90px 0 0;
    text-align:center;padding-top:32px}
  .trailer-title{font-family:"Oswald",sans-serif;font-weight:500;font-size:20px;line-height:22px;text-transform:uppercase}
  .trailer-spec{font-size:13px;line-height:16px;margin-top:2px}
  .rate{position:absolute;left:0;width:232px;display:flex}
  .rate-week{top:200px;height:146px}
  .rate-weekend{top:350px;height:170px}
  .rate-tab{width:36px;margin:14px 0;border-radius:10px 0 0 10px;display:flex;align-items:center;justify-content:center}
  .rate-tab span{writing-mode:vertical-rl;transform:rotate(180deg);font-weight:700;font-size:14px;color:var(--white)}
  .rate-week .rate-tab{background:var(--coral)}
  .rate-weekend .rate-tab{background:var(--teal)}
  .rate-card{flex:1;border-radius:12px;padding:6px;text-align:center;color:var(--ink)}
  .rate-week .rate-card{background:var(--teal)}
  .rate-weekend .rate-card{background:var(--coral)}
  .rate-inner{height:100%;border-radius:8px;padding:10px 10px 0}
  .rate-week .rate-inner{background:var(--teal-light)}
  .rate-weekend .rate-inner{background:var(--coral-light);padding-top:16px}
  .rate-days{font-size:14px;line-height:16px;padding-bottom:8px;border-bottom:1px dashed #8a86d6}
  .rate-price{font-family:"Oswald",sans-serif;font-weight:500;font-size:23px;line-height:30px;margin-top:6px}
  .rate-weekend .rate-price{line-height:34px}
  .rate-price sup{font-size:11px;vertical-align:top;position:relative;top:2px}
  .contact-bar{position:absolute;left:59px;top:1114px;display:flex;align-items:center;width:730px}
  .book-now{background:var(--coral);color:var(--white);font-weight:700;font-size:14px;letter-spacing:2px;
    padding:8px 0;width:136px;text-align:center;border-radius:12px}
  .contact-item{display:flex;align-items:center;gap:8px;font-weight:500}
  .contact-phone{margin-left:18px;font-size:21px}
  .divider{width:2px;height:18px;background:var(--teal);margin:0 15px}
  .contact-web{font-size:18px}
  .contact-item svg{width:18px;height:18px}
  .foot-band{position:absolute;left:0;top:1152px;width:806px;height:48px;background:#000}
</style>
</head>
<body>
<main class="flyer">
  <div class="sun-glow"></div>
  <div class="hero-photo" role="img" aria-label="Photo: white SUV towing a flatbed car trailer loaded with a green and a blue classic car on a desert highway, mountains and yellow fields behind"></div>

  <div class="brand">
    <span class="brand-dot"></span>
    <span class="brand-name">K&amp;R Trailer Rental</span>
  </div>

  <h1 class="headline">
    <span class="headline-car">CAR</span>
    <span class="headline-or">OR</span>
    <span class="headline-equipment">EQUIPMENT</span>
    <span class="headline-trailers">TRAILERS</span>
  </h1>

  <p class="offer-intro">
    <span class="thin">These are</span>
    <span class="thin">the trailers</span>
    <span class="bold">We have</span>
    <span class="bold">available to</span>
    <span class="bold">offer you</span>
  </p>

  <ul class="features">
    <li class="feature">
      <svg viewBox="0 0 34 34"><rect x="3" y="6" width="26" height="24" rx="2" fill="#fff"/><rect x="3" y="6" width="26" height="7" fill="#4a8fd8"/><rect x="8" y="3" width="3" height="7" fill="#e06a3a"/><rect x="21" y="3" width="3" height="7" fill="#e06a3a"/><circle cx="23" cy="24" r="7" fill="#f0a23a"/><path d="M19.5 24l2.5 2.5 4.5-4.5" stroke="#fff" stroke-width="2" fill="none"/></svg>
      <span>Online<br>Booking</span>
    </li>
    <li class="feature">
      <svg viewBox="0 0 34 34"><circle cx="14" cy="14" r="10" fill="#4ab7e8" stroke="#fff" stroke-width="3"/><path d="M21 21l9 9" stroke="#f0b23a" stroke-width="5" stroke-linecap="round"/></svg>
      <span>Transparency<br>Policy</span>
    </li>
    <li class="feature">
      <svg viewBox="0 0 34 34"><path d="M10 20l-5 12 6-3 3 5 4-11z M24 20l5 12-6-3-3 5-4-11z" fill="#e89a3a"/><circle cx="17" cy="14" r="11" fill="#f3c451"/><circle cx="17" cy="14" r="7" fill="#f8dc8a"/></svg>
      <span>Top Rated</span>
    </li>
  </ul>

  <section class="trailer trailer-car">
    <div class="trailer-photo" role="img" aria-label="Photo: car trailer hitched in a parking lot"></div>
    <div class="trailer-head">
      <h2 class="trailer-title">Car Trailer</h2>
      <p class="trailer-spec">TK 20' X 7' Car Hauler</p>
    </div>
    <div class="rate rate-week">
      <div class="rate-tab"><span>Week Rates</span></div>
      <div class="rate-card"><div class="rate-inner">
        <p class="rate-days">Monday through<br>Thursday</p>
        <p class="rate-price"><sup>$</sup>85/DAY*<br><sup>$</sup>350/WEEK*</p>
      </div></div>
    </div>
    <div class="rate rate-weekend">
      <div class="rate-tab"><span>Weekend Rates</span></div>
      <div class="rate-card"><div class="rate-inner">
        <p class="rate-days">Friday through<br>Sunday</p>
        <p class="rate-price"><sup>$</sup>85/DAY*<br><sup>$</sup>200/WEEKEND*</p>
      </div></div>
    </div>
  </section>

  <section class="trailer trailer-equip">
    <div class="trailer-photo" role="img" aria-label="Photo: long flatbed equipment trailer parked on a lot"></div>
    <div class="trailer-head">
      <h2 class="trailer-title">Equipment Trailer</h2>
      <p class="trailer-spec">Strider 30' x 7' 14k lbs</p>
    </div>
    <div class="rate rate-week">
      <div class="rate-tab"><span>Week Rates</span></div>
      <div class="rate-card"><div class="rate-inner">
        <p class="rate-days">Monday through<br>Thursday</p>
        <p class="rate-price"><sup>$</sup>100/DAY*<br><sup>$</sup>500/WEEK*</p>
      </div></div>
    </div>
    <div class="rate rate-weekend">
      <div class="rate-tab"><span>Weekend Rates</span></div>
      <div class="rate-card"><div class="rate-inner">
        <p class="rate-days">Friday through<br>Sunday</p>
        <p class="rate-price"><sup>$</sup>100/DAY*<br><sup>$</sup>250/WEEKEND*</p>
      </div></div>
    </div>
  </section>

  <div class="contact-bar">
    <span class="book-now">BOOK NOW</span>
    <span class="contact-item contact-phone">
      <svg viewBox="0 0 24 24"><path d="M6.6 10.8a15.5 15.5 0 006.6 6.6l2.2-2.2a1 1 0 011-.25 11.4 11.4 0 003.6.6 1 1 0 011 1V20a1 1 0 01-1 1A17 17 0 013 4a1 1 0 011-1h3.5a1 1 0 011 1 11.4 11.4 0 00.6 3.6 1 1 0 01-.25 1z" fill="#4aa4aa"/></svg>
      (555)613-2890
    </span>
    <span class="divider"></span>
    <span class="contact-item contact-web">
      <svg viewBox="0 0 24 24"><circle cx="12" cy="12" r="9" fill="none" stroke="#4aa4aa" stroke-width="2"/><ellipse cx="12" cy="12" rx="4" ry="9" fill="none" stroke="#4aa4aa" stroke-width="2"/><path d="M3 12h18" stroke="#4aa4aa" stroke-width="2"/></svg>
      www.kandrtrailer-example.com
    </span>
  </div>

  <div class="foot-band"></div>
</main>
</body>
</html>
```